Provide bookkeeping and accounting services to small and growing businesses

We need website and logo design using the name Dornaby as the logo.
The target audience are small companies and startups who need:
1) Simple bookkeeping services
2) Accounting advice that only someone with many years of senior financial experience as a CPA can provide.

The services are provided by two individuals. each of whom specialize in one of the areas.

We want the website to be clean without a lot of visual distraction but don't know how to make a boring subject interesting. We believe our potential clients, small business owners, need to find what they want quickly and easily without a lot of verbiage or distractions.

We've attached a draft of the homepage and have completed the text on most of the other pages.

Target Market(s)

small and early stage growth companies in San Diego North County

Industry/Entity Type

Accounting

Number of Pages Required

1 page

Font styles to use
Sans Serif

Colors
86cfc6
33b8a4
85cae6

Requirements
Must have
• We need a design for the website homepage that includes the name Dornaby as the logo. Must include a design for the name.
• Must have color in teal or greenish blue.
Nice to have
• White background, clean, clear, uncluttered.
• We would like to use the design in a Theme on a WordPress website. Themes Paper Lantern and Quiet Harbour are appealing to us.
Should not have
• Moving pictures

```html
<!DOCTYPE html>
<html lang="en">
<head>
<meta charset="utf-8">
<title>Dornaby Accounting &amp; Bookkeeping</title>
<link rel="stylesheet" href="https://fonts.googleapis.com/css2?family=Open+Sans:wght@400;600;700&family=Roboto:wght@300;400&family=Roboto+Condensed:wght@700&display=swap">
<style>
:root{
  --teal:#33b8a4;
  --teal-soft:#86cfc6;
  --ink:#3a3f44;
  --text:#555a5f;
  --muted:#8a8f94;
  --line:#e2e2e2;
  --footer-bg:#f0f1f1;
  --bar-bg:#323435;
  --white:#ffffff;
}
*{box-sizing:border-box;margin:0;padding:0}
html,body{width:944px;height:1200px;overflow:hidden;background:var(--white);font-family:"Open Sans",sans-serif;color:var(--text)}
.page{position:relative;width:944px;height:1200px}

.site-header{position:absolute;left:0;top:0;width:944px;height:74px;background:var(--white)}
.brand{position:absolute;left:77px;top:16px;display:flex;align-items:center;gap:8px}
.brand-dot{width:43px;height:43px;border-radius:50%;background:var(--teal)}
.brand-name{font-weight:700;font-size:23px;letter-spacing:1.5px;color:var(--ink);line-height:24px}
.brand-tag{font-size:11px;color:var(--ink);line-height:14px;letter-spacing:.3px}
.main-nav{position:absolute;top:33px;left:0;width:944px}
.main-nav a{position:absolute;font-size:11px;letter-spacing:.5px;color:var(--ink);text-decoration:none;white-space:nowrap}
.main-nav a.active{color:var(--teal)}

.hero{position:absolute;left:0;top:74px;width:944px;height:434px;background:linear-gradient(120deg,#6b6f74 0%,#8a8d90 35%,#a9aba9 60%,#7e8288 100%)}
.hero-title{position:absolute;left:480px;top:200px;font-family:"Roboto Condensed",sans-serif;font-weight:700;font-size:32px;line-height:34px;color:var(--white);letter-spacing:.3px}
.hero-arrow{position:absolute;top:192px}

.services{position:absolute;left:0;top:540px;width:944px}
.section-title{position:absolute;left:0;top:10px;width:944px;text-align:center;font-family:"Roboto",sans-serif;font-weight:300;font-size:32px;color:var(--ink)}
.section-rule{position:absolute;left:443px;top:51px;width:58px;height:1px;background:var(--teal)}
.service{position:absolute;top:82px;width:250px}
.service-icon{position:absolute;left:0;top:4px}
.service-head{position:absolute;left:41px;top:0;white-space:nowrap}
.service-name{font-family:"Roboto",sans-serif;font-size:16px;color:var(--ink);line-height:20px}
.service-sub{font-size:8.5px;color:var(--ink);line-height:12px}
.service-photo{position:absolute;left:0;top:48px;width:250px;height:144px;border:1px solid var(--line);padding:4px;background:var(--white)}
.service-photo div{width:100%;height:100%}
.service-text{position:absolute;left:0;top:208px;width:250px;font-size:8.6px;line-height:16px;color:var(--text)}

.site-footer{position:absolute;left:0;top:930px;width:944px;height:222px;background:var(--footer-bg)}
.foot-brand{position:absolute;left:77px;top:76px;width:106px;text-align:center}
.foot-brand .brand-dot{margin:0 auto 4px;width:46px;height:46px}
.foot-brand .brand-name{font-size:18px;line-height:20px;letter-spacing:1.2px}
.foot-brand .brand-tag{font-size:8px;line-height:11px}
.foot-heading{position:absolute;top:44px;font-family:"Roboto",sans-serif;font-weight:300;font-size:14px;color:var(--ink);white-space:nowrap}
.newsletter-copy{position:absolute;left:248px;top:78px;width:206px;font-size:8.5px;line-height:15px;color:var(--text);text-align:justify}
.field{position:absolute;left:248px;width:206px;height:33px;background:var(--white);border:1px solid var(--line);font-size:8.5px;color:var(--ink);padding:10px 11px}
.subscribe{position:absolute;left:378px;top:152px;width:76px;height:32px;background:var(--teal);color:var(--white);font-size:10px;text-align:center;line-height:32px}
.foot-divider{position:absolute;top:36px;width:1px;height:150px;background:#e4e5e5}
.contact-item{position:absolute;left:542px;font-size:10px;line-height:16px;color:var(--text);white-space:nowrap}
.contact-item svg{position:absolute;left:0;top:3px}
.contact-item span{display:block;padding-left:20px}
.quick-links{position:absolute;left:790px;top:72px;list-style:none}
.quick-links li{font-size:8.8px;line-height:17.6px;color:var(--text)}

.legal-bar{position:absolute;left:0;top:1152px;width:944px;height:48px;background:var(--bar-bg);text-align:center;line-height:48px;font-size:8.6px;color:var(--white)}
</style>
</head>
<body>
<div class="page">

  <header class="site-header">
    <div class="brand">
      <div class="brand-dot"></div>
      <div>
        <div class="brand-name">DORNABY</div>
        <div class="brand-tag">Accounting &amp; Bookkeeping</div>
      </div>
    </div>
    <nav class="main-nav">
      <a class="active" style="left:370px">HOME</a>
      <a style="left:438px">ABOUT US</a>
      <a style="left:525px">SERVICES</a>
      <a style="left:607px">EXPERIENCE</a>
      <a style="left:704px">RESOURCES</a>
      <a style="left:800px">CONTACT US</a>
    </nav>
  </header>

  <section class="hero" role="img" aria-label="Photo of a laptop on a desk and hands holding printed financial charts">
    <svg class="hero-arrow" style="left:27px" width="24" height="48" viewBox="0 0 24 48"><polyline points="23,1 1,24 23,47" fill="none" stroke="#e8e8e8" stroke-width="1"/></svg>
    <h1 class="hero-title">DORNABY ACCOUNTING<br>&amp; BOOKKEEPING</h1>
    <svg class="hero-arrow" style="left:890px" width="24" height="48" viewBox="0 0 24 48"><polyline points="1,1 23,24 1,47" fill="none" stroke="#e8e8e8" stroke-width="1"/></svg>
  </section>

  <section class="services">
    <h2 class="section-title">Our Services</h2>
    <div class="section-rule"></div>

    <article class="service" style="left:77px">
      <svg class="service-icon" width="34" height="28" viewBox="0 0 34 28"><rect x="1" y="1" width="32" height="20" rx="2" fill="none" stroke="#33b8a4" stroke-width="2.5"/><rect x="14" y="21" width="6" height="4" fill="#33b8a4"/><rect x="9" y="25" width="16" height="3" rx="1" fill="#33b8a4"/></svg>
      <div class="service-head"><div class="service-name">Book Keeping Services</div><div class="service-sub">Lorem ipsum dolor sit amet,</div></div>
      <div class="service-photo"><div role="img" aria-label="Photo of hands using a tablet with a stylus" style="background:linear-gradient(135deg,#cfdbe6,#8fb0cc 55%,#e6e8ea)"></div></div>
      <p class="service-text">Lorem ipsum dolor sit amet, consectetur adipisicing elit, sed do eiusmod tempor incididunt ut labore et dolore magna aliqua. Ut enim ad minim veniam,</p>
    </article>

    <article class="service" style="left:346px">
      <svg class="service-icon" width="28" height="28" viewBox="0 0 28 28"><path d="M10 2h8l-3 5h-2z" fill="#33b8a4"/><path d="M10 8h8c6 4 9 10 9 15a4 4 0 0 1-4 4H5a4 4 0 0 1-4-4c0-5 3-11 9-15z" fill="#33b8a4"/><text x="14" y="23" text-anchor="middle" font-family="Open Sans,sans-serif" font-size="11" font-weight="700" fill="#fff">$</text></svg>
      <div class="service-head"><div class="service-name">Financial Planning</div><div class="service-sub">Lorem ipsum dolor sit amet,</div></div>
      <div class="service-photo"><div role="img" aria-label="Photo of a hand touching glowing dollar signs and a rising bar chart" style="background:linear-gradient(135deg,#4a5878,#8d9bbd 55%,#c9cde0)"></div></div>
      <p class="service-text">Lorem ipsum dolor sit amet, consectetur adipisicing elit, sed do eiusmod tempor incididunt ut labore et dolore magna aliqua. Ut enim ad minim veniam,</p>
    </article>

    <article class="service" style="left:615px">
      <svg class="service-icon" width="32" height="26" viewBox="0 0 32 26"><circle cx="16" cy="6" r="5" fill="#33b8a4"/><circle cx="6" cy="9" r="4" fill="#33b8a4"/><circle cx="26" cy="9" r="4" fill="#33b8a4"/><path d="M8 25c0-7 4-11 8-11s8 4 8 11z" fill="#33b8a4"/><path d="M0 23c0-5 3-8 6-8 2 0 3 1 4 2-2 2-3 4-3 6z" fill="#33b8a4"/><path d="M32 23c0-5-3-8-6-8-2 0-3 1-4 2 2 2 3 4 3 6z" fill="#33b8a4"/></svg>
      <div class="service-head"><div class="service-name">Accounting Advice</div><div class="service-sub">Lorem ipsum dolor sit amet,</div></div>
      <div class="service-photo"><div role="img" aria-label="Photo of two people reviewing documents at a desk" style="background:linear-gradient(135deg,#2c3340,#a9b9cc 50%,#eef0f2)"></div></div>
      <p class="service-text">Lorem ipsum dolor sit amet, consectetur adipisicing elit, sed do eiusmod tempor incididunt ut labore et dolore magna aliqua. Ut enim ad minim veniam,</p>
    </article>
  </section>

  <footer class="site-footer">
    <div class="foot-brand">
      <div class="brand-dot"></div>
      <div class="brand-name">DORNABY</div>
      <div class="brand-tag">Accounting &amp; Bookkeeping</div>
    </div>

    <h3 class="foot-heading" style="left:248px">SIGN UP FOR NEWSLETTER</h3>
    <p class="newsletter-copy">Excepteur sint occaecat cupidatat non proident, sunt in culpa qui officia deserunt</p>
    <div class="field" style="top:111px">Enter Name</div>
    <div class="field" style="top:152px">Enter Email</div>
    <div class="subscribe">SUBSCRIBE</div>

    <div class="foot-divider" style="left:498px"></div>
    <div class="foot-divider" style="left:754px"></div>

    <h3 class="foot-heading" style="left:540px">CONTACTS US</h3>
    <div class="contact-item" style="top:76px">
      <svg width="11" height="13" viewBox="0 0 11 13"><path d="M5.5 0A5 5 0 0 0 .5 5c0 3.5 5 8 5 8s5-4.5 5-8a5 5 0 0 0-5-5z" fill="#b5b9bc"/><circle cx="5.5" cy="5" r="2" fill="#f0f1f1"/></svg>
      <span>Harbor Lane, North County<br>California</span>
    </div>
    <div class="contact-item" style="top:122px;font-size:11px">
      <svg width="11" height="11" viewBox="0 0 11 11"><path d="M2 0l2 2.5-1.2 1.6c.8 1.6 2 2.8 3.6 3.6L8 6.5 11 8.5 9.5 11C4.5 10.5.5 6.5 0 1.5z" fill="#b5b9bc"/></svg>
      <span>Phone: (555) 014-2207</span>
    </div>
    <div class="contact-item" style="top:146px">
      <svg width="11" height="8" viewBox="0 0 11 8"><rect width="11" height="8" fill="#b5b9bc"/><polyline points="0,0 5.5,4.5 11,0" fill="none" stroke="#f0f1f1" stroke-width="1"/></svg>
      <span>info@dornabyaccounting.com</span>
    </div>

    <h3 class="foot-heading" style="left:788px">QUICK LINKS</h3>
    <ul class="quick-links">
      <li>Home</li><li>About Us</li><li>Services</li><li>Experience</li><li>Resources</li><li>Contact Us</li>
    </ul>
  </footer>

  <div class="legal-bar">©2015 - 2016 Dornaby Accounting &amp; Bookkeeping, All Rights Reserved.</div>
</div>
</body>
</html>
```